Ft Darrow Cider Co needs web page design

Need a web design for a ecommerce website for honey wine. We make honeywine (a dessert type wine made with honey). Our initial product is a standard honey wine and pyment and a cyser. We have all our logos and designs but need to place in web design to reflect our product and ecommerce. We want the file labeled "chatwave cover logo 2" as the banner for the site.

Target Market(s)

People who drink sweeter wines, dessert wine, or non traditional/non-grape wines. Cizer drinkers. 20-60 years old.

Requirements
Must have
• The "bee button" picture as the button image. The "cw cover 2" image as the page banner. Open, bright feel/coloring. Coloring featuring gold, red colors that reflect our logos. PLEASE USE THE CHATWAVE COVER 2 AS OR ON LABEL BANNER TOP OF WEB PAGE. Files 2-3-4 and 5 are our first labels. Those are what will be on bottles when we sale them. This should reflect on web page. We will not use file 8 labels but the graphics could be used on website. There for inspiration.
Nice to have
• Reflect the fonts that are on our logos as close as possible.
Should not have
• Not too much black, red, or honey references. We don't want the page to be too saturated with any of those elements. Not cluttered with imagery.

```html
<!DOCTYPE html>
<html lang="en">
<head>
<meta charset="utf-8">
<title>Ft Darrow Cider Co — Honey Wine</title>
<link rel="stylesheet" href="https://fonts.googleapis.com/css2?family=Poppins:wght@400;500;600;700&family=Raleway:wght@300;400;500;600;700;800&display=swap">
<style>
:root{
  --maroon:#8e1232;
  --gold:#f39320;
  --coin:#c9a75a;
  --ink:#4f4f4f;
  --text:#555;
  --pyment:#b07690;
  --cyser:#55940f;
  --honey:#f59a23;
  --white:#fff;
}
*{box-sizing:border-box;margin:0;padding:0}
html,body{width:1200px;height:3069px;overflow:hidden;background:var(--white)}
body{position:relative;font-family:"Raleway",sans-serif;color:var(--text)}

/* header */
.site-nav{position:absolute;top:36px;height:42px;border-top:1px solid var(--maroon);border-bottom:1px solid var(--maroon);display:flex;align-items:center;gap:24px;font-family:"Poppins",sans-serif;font-size:14px;color:#333;z-index:3}
.site-nav a{color:inherit;text-decoration:none}
.nav-left{left:143px;width:335px}
.nav-right{left:722px;width:334px;justify-content:flex-end}
.account-btn{background:var(--maroon);color:#fff!important;border-radius:14px;padding:4px 13px;font-size:13px}
.brand{position:absolute;left:478px;top:56px;width:244px;text-align:center;z-index:3}
.brand-name{font-family:"Raleway",sans-serif;font-weight:500;font-size:24px;letter-spacing:3px;color:var(--maroon);line-height:28px}
.brand-sub{font-family:"Raleway",sans-serif;font-weight:500;font-size:14px;letter-spacing:5px;color:#d08a3a;margin-top:2px}

/* hero */
.hero{position:absolute;left:0;top:0;width:1200px;height:620px;background:linear-gradient(180deg,#ede3e8 0%,#e7dfe3 16%,#a9a6a8 38%,#6a686a 58%,#4f4d4f 76%,#eeeced 90%,#fff 100%)}
.hero-photo{position:absolute;left:596px;top:119px;width:604px;height:470px;background:linear-gradient(90deg,rgba(70,50,55,0) 0%,rgba(60,40,48,.45) 25%,rgba(50,35,40,.55) 60%,rgba(120,90,80,.35) 85%,rgba(120,90,80,0) 100%);-webkit-mask-image:linear-gradient(180deg,transparent 0%,#000 15%,#000 85%,transparent 100%);mask-image:linear-gradient(180deg,transparent 0%,#000 15%,#000 85%,transparent 100%)}
.hero-title{position:absolute;left:143px;top:230px;font-family:"Poppins",sans-serif;font-weight:700;font-size:39px;line-height:50px;color:var(--gold)}
.hero-sub{position:absolute;left:145px;top:284px;font-family:"Poppins",sans-serif;font-size:21px;color:var(--maroon)}

.btn{position:absolute;display:flex;align-items:center;justify-content:space-between;background:var(--maroon);color:#fff;border:1px solid #fff;outline:1px solid var(--maroon);font-family:"Poppins",sans-serif;font-weight:500;letter-spacing:1px;padding:0 8px 0 13px;text-decoration:none;z-index:4}
.coin{width:24px;height:24px;border-radius:50%;background:radial-gradient(circle at 40% 35%,#e3cb8c,var(--coin) 60%,#a98a3f)}

/* about */
.about-kicker{position:absolute;left:0;width:1200px;top:662px;text-align:center;font-size:25px;letter-spacing:2px;color:#444}
.about-title{position:absolute;left:0;width:1200px;top:692px;text-align:center;font-size:49px;font-weight:800;letter-spacing:4px;color:var(--ink)}
.rule{position:absolute;height:2px;background:#444}
.about-copy{position:absolute;left:280px;width:640px;top:783px;text-align:center;font-size:13px;line-height:20px;color:#555}

/* product cards */
.card{position:absolute;left:144px;width:912px;height:398px}
.card-photo{position:absolute;top:0;height:398px}
.card-frame{position:absolute;left:14px;top:16px;width:882px;height:367px;border:7px solid #fff}
.card-copy{position:absolute;top:52px;width:380px;text-align:center;color:#fff}
.card-copy h2{font-weight:500;font-size:33px;letter-spacing:3px;line-height:40px}
.card-copy h3{font-weight:500;font-size:21px;letter-spacing:2px;margin-top:10px}
.card-copy .mini-rule{width:48px;height:1px;background:rgba(255,255,255,.8);margin:20px auto 22px}
.card-copy p{font-size:12.5px;line-height:20px}
.card-copy .price{font-family:"Poppins",sans-serif;font-weight:600;font-size:20px;letter-spacing:2px;margin-top:18px}
.product-shot{position:absolute;z-index:2}
.soft-edge{-webkit-mask-image:radial-gradient(closest-side,#000 55%,transparent 100%);mask-image:radial-gradient(closest-side,#000 55%,transparent 100%)}

/* footer */
.footer{position:absolute;left:0;top:2550px;width:1200px;height:519px}
.f-rule{position:absolute;left:144px;width:912px;height:1px;background:rgba(255,255,255,.35)}
.f-brand{position:absolute;left:146px;top:2712px}
.f-brand .brand-name{color:#fff;font-size:29px;letter-spacing:4px;line-height:34px}
.f-brand .brand-sub{color:#fff;font-size:17px;letter-spacing:8px;padding-left:66px}
.newsletter-label{position:absolute;left:673px;top:2683px;font-family:"Poppins",sans-serif;font-weight:500;font-size:15px;color:#fff;letter-spacing:.5px}
.email-field{position:absolute;left:673px;top:2713px;width:252px;height:36px;border:1px solid rgba(255,255,255,.6);border-radius:3px;padding:0 14px;line-height:34px;font-family:"Poppins",sans-serif;font-size:14px;color:rgba(255,255,255,.7)}
.signup-btn{position:absolute;left:934px;top:2713px;width:121px;height:36px;background:var(--maroon);border:2px solid #fff;border-radius:3px;color:#fff;font-family:"Poppins",sans-serif;font-weight:500;font-size:15px;text-align:center;line-height:32px}
.f-col{position:absolute;top:2812px;color:#fff;font-family:"Poppins",sans-serif}
.f-col h4{font-weight:400;font-size:17px;margin-bottom:16px}
.f-col li{list-style:none;font-size:13.5px;line-height:29px}
.f-contact li{font-weight:600;font-size:14px;letter-spacing:.3px}
.copyright{position:absolute;left:142px;top:3025px;font-family:"Poppins",sans-serif;font-size:13px;color:#fff}
.socials{position:absolute;left:927px;top:3019px;display:flex;gap:5px}
.socials span{width:28px;height:28px;border:1.5px solid #fff;border-radius:50%}
</style>
</head>
<body>

<section class="hero">
  <div class="hero-photo" role="img" aria-label="Two honey wine bottles with a glass of red and a glass of white wine beside dark and red grapes"></div>
  <h1 class="hero-title">FT DARROW</h1>
  <p class="hero-sub">A dessert type wine made with honey</p>
  <a class="btn" style="left:143px;top:330px;width:143px;height:41px;font-size:15px">Buy Now <span class="coin" role="img" aria-label="Gold bee button"></span></a>
</section>

<nav class="site-nav nav-left"><a>Home</a><a>Shop</a><a>Our Store</a><a>Testimonials</a></nav>
<div class="brand">
  <div class="brand-name">FT DARROW</div>
  <div class="brand-sub">CIDER CO</div>
</div>
<nav class="site-nav nav-right"><a>Articles</a><a>Contact Us</a><a class="account-btn">My Account</a></nav>

<p class="about-kicker">About</p>
<h2 class="about-title">FT DARROW</h2>
<div class="rule" style="left:571px;top:760px;width:58px"></div>
<p class="about-copy">Lorem Ipsum is simply dummy text of the printing and typesetting industry. Lorem Ipsum has been the industry's standard dummy text ever since the 1500s, when an unknown printer took a galley of type and scrambled it to make a type specimen book. It has survived not only five centuries, but also the leap into electronic typesetting, remaining essentially unchanged. It was popularised in the 1960s with the release of Letraset sheets containing Lorem Ipsum passages, and more recently with desktop publishing software like Aldus PageMaker including versions of Lorem Ipsum.</p>
<a class="btn" style="left:529px;top:943px;width:142px;height:34px;font-size:13px">Read More <span class="coin" role="img" aria-label="Gold bee button"></span></a>

<!-- pyment -->
<section class="card" style="top:1058px;background:var(--pyment)">
  <div class="card-photo" style="left:0;width:334px;background:linear-gradient(160deg,#c9a070 0%,#6e6a88 35%,#4c5584 65%,#8f9a6a 100%)" role="img" aria-label="Bunch of dark blue grapes on the vine"></div>
  <div class="card-frame"></div>
  <div class="card-copy" style="left:430px">
    <h2>PYMENT</h2><h3>Grape Honey Wine</h3><div class="mini-rule"></div>
    <p>Lorem Ipsum is simply dummy text of the printing and typesetting industry. Lorem Ipsum has been the industry's standard dummy text ever since the 1500s,</p>
    <p class="price">$562.00</p>
  </div>
  <a class="btn" style="left:560px;top:287px;width:118px;height:34px;font-size:13px">Buy Now <span class="coin" role="img" aria-label="Gold bee button"></span></a>
</section>
<div class="product-shot soft-edge" style="left:420px;top:1138px;width:130px;height:342px;background:linear-gradient(180deg,rgba(90,30,45,.35),rgba(40,30,35,.45))" role="img" aria-label="Pyment bottle with honeycomb label"></div>
<div class="product-shot soft-edge" style="left:941px;top:1317px;width:209px;height:187px;background:linear-gradient(135deg,rgba(110,140,80,.5),rgba(70,75,120,.5))" role="img" aria-label="Small bunch of grapes with leaves"></div>

<!-- cyser -->
<section class="card" style="top:1534px;background:var(--cyser)">
  <div class="card-photo" style="left:577px;width:335px;background:linear-gradient(160deg,#6fbf22,#5aa61a 50%,#4a8c14)" role="img" aria-label="Pile of green apples"></div>
  <div class="card-frame"></div>
  <div class="card-copy" style="left:85px">
    <h2>CYZER</h2><h3>Apple Honey Wine</h3><div class="mini-rule"></div>
    <p>Lorem Ipsum is simply dummy text of the printing and typesetting industry. Lorem Ipsum has been the industry's standard dummy text ever since the 1500s,</p>
    <p class="price">$562.00</p>
  </div>
  <a class="btn" style="left:223px;top:286px;width:119px;height:35px;font-size:13px">Buy Now <span class="coin" role="img" aria-label="Gold bee button"></span></a>
</section>
<div class="product-shot soft-edge" style="left:655px;top:1615px;width:130px;height:340px;background:linear-gradient(180deg,rgba(90,30,45,.35),rgba(40,50,30,.45))" role="img" aria-label="Cyser bottle with honeycomb label"></div>
<div class="product-shot soft-edge" style="left:119px;top:1776px;width:155px;height:179px;background:linear-gradient(135deg,rgba(170,220,90,.6),rgba(100,170,40,.55))" role="img" aria-label="Single green apple with a leaf"></div>

<!-- honey wine -->
<section class="card" style="top:1985px;background:var(--honey)">
  <div class="card-photo" style="left:0;width:334px;background:linear-gradient(160deg,#8a6a48 0%,#b86a22 45%,#9a4a14 75%,#6a4a30 100%)" role="img" aria-label="Honey dripping from a dipper into a glass jar beside honeycomb"></div>
  <div class="card-frame"></div>
  <div class="card-copy" style="left:430px">
    <h2>HONEY WINE</h2><h3>Wine Made from Pure Honey</h3><div class="mini-rule"></div>
    <p>Lorem Ipsum is simply dummy text of the printing and typesetting industry. Lorem Ipsum has been the industry's standard dummy text ever since the 1500s,</p>
    <p class="price">$562.00</p>
  </div>
  <a class="btn" style="left:561px;top:287px;width:120px;height:35px;font-size:13px">Buy Now <span class="coin" role="img" aria-label="Gold bee button"></span></a>
</section>
<div class="product-shot soft-edge" style="left:420px;top:2068px;width:130px;height:339px;background:linear-gradient(180deg,rgba(90,30,45,.35),rgba(60,40,20,.45))" role="img" aria-label="Honey wine bottle with honeycomb label"></div>
<div class="product-shot soft-edge" style="left:971px;top:2199px;width:135px;height:214px;background:linear-gradient(180deg,rgba(200,150,60,.45),rgba(245,175,40,.6))" role="img" aria-label="Jar of honey with a wooden dipper"></div>

<footer class="footer">
  <svg width="1200" height="519" viewBox="0 0 1200 519" aria-hidden="true" style="position:absolute;left:0;top:0">
    <defs>
      <linearGradient id="footerShade" x1="0" y1="0" x2="0" y2="1">
        <stop offset="0" stop-color="#3a0b14"/><stop offset=".3" stop-color="#6b1322"/><stop offset="1" stop-color="#4a0a16"/>
      </linearGradient>
    </defs>
    <path d="M0 40 L60 30 L120 42 L190 20 L260 36 L340 14 L420 32 L500 8 L580 28 L660 6 L740 30 L820 12 L900 34 L980 10 L1060 30 L1130 14 L1200 26 L1200 519 L0 519 Z" fill="url(#footerShade)"/>
  </svg>
</footer>
<div class="f-rule" style="top:2643px"></div>
<div class="f-brand">
  <div class="brand-name">FT DARROW</div>
  <div class="brand-sub">CIDER CO</div>
</div>
<p class="newsletter-label">Sign Up Newsletter</p>
<div class="email-field">Your Email</div>
<div class="signup-btn">SIGN UP</div>
<div class="f-rule" style="top:2789px"></div>

<div class="f-col" style="left:144px"><h4>LINKS</h4><ul><li>Home</li><li>Shop</li><li>Our Store</li><li>Testimonials</li></ul></div>
<div class="f-col" style="left:360px"><h4>SUPPORT</h4><ul><li>Terms and Conditions</li><li>Privacy Policy</li><li>Return Policy</li></ul></div>
<div class="f-col" style="left:639px"><h4>ABOUT</h4><ul><li>About</li><li>News</li><li>Contact</li><li>News</li></ul></div>
<div class="f-col f-contact" style="left:800px;top:2809px"><h4>CONTACT US</h4>
  <ul><li>+555-204-7781</li><li style="margin-top:8px">hello@ftdarrowcider.example</li><li style="margin-top:12px">42 Orchard Lane Road</li><li>Millbrook, Westfield 00000</li></ul></div>

<div class="f-rule" style="top:2997px"></div>
<p class="copyright">FT DARROW © 2021 All Rights Reserved.</p>
<div class="socials" aria-label="Social links"><span></span><span></span><span></span><span></span></div>

</body>
</html>
```